Belmont Ridge Business Card Design Project

We have recently rebranded and would like to design new business cards that incorporate the corporate logo - double sided cards with corporate logo on one side and contact details on the other

Target Market(s)

Sophisticated and high net worth investors and finance industry professionals

Industry/Entity Type

Funds Management

Contact Information for Business Card

The card should prominently feature the company name and logo. Other details will be standard contact details for each staff member - name, address, phone, email, website

Colors
0054AA
0677BA
7BADD7
CADEEF
E8F1F8

Requirements
Must have
• Double-sided design with one side prominently featuring the corporate logo and the other side with all standard contact details

```html
<!DOCTYPE html>
<html lang="en">
<head>
<meta charset="utf-8">
<title>Belmont Ridge – Business Card</title>
<link href="https://fonts.googleapis.com/css2?family=Cinzel:wght@500&family=Jost:wght@400;500&family=Open+Sans:wght@400&display=swap" rel="stylesheet">
<style>
  :root {
    --backdrop: #ababab;
    --navy: #224777;
    --navy-light: #2b5a94;
    --ink: #1f4474;
    --grey-text: #777777;
    --logo-grey: #9a9a9a;
    --dark: #333333;
    --white: #ffffff;
  }
  html, body {
    margin: 0;
    padding: 0;
    width: 1200px;
    height: 1000px;
    overflow: hidden;
    background: var(--backdrop);
  }
  .stage {
    position: relative;
    width: 1200px;
    height: 1000px;
  }
  .card {
    position: absolute;
    width: 514px;
    height: 296px;
    box-shadow: 0 18px 40px rgba(0,0,0,0.35);
    overflow: hidden;
  }
  .card-front {
    left: 57px;
    top: 339px;
    background: var(--navy);
  }
  .front-pattern {
    position: absolute;
    inset: 0;
    background: linear-gradient(180deg, rgba(43,90,148,0.35) 0%, rgba(34,71,119,0) 55%),
                linear-gradient(90deg, rgba(34,71,119,0) 40%, rgba(43,90,148,0.45) 100%);
  }
  .front-name {
    position: absolute;
    left: 0;
    right: 0;
    top: 150px;
    text-align: center;
    font-family: "Cinzel", serif;
    font-weight: 500;
    font-size: 40px;
    color: var(--white);
    letter-spacing: 0.5px;
  }
  .card-back {
    left: 614px;
    top: 338px;
    background: var(--white);
  }
  .back-band {
    position: absolute;
    left: 0;
    right: 0;
    bottom: 0;
    height: 4px;
    background: var(--navy);
  }
  .back-logo {
    position: absolute;
    left: 29px;
    top: 33px;
    font-family: "Cinzel", serif;
    font-weight: 500;
    font-size: 16px;
    color: var(--logo-grey);
  }
  .person-name {
    position: absolute;
    left: 28px;
    top: 87px;
    font-family: "Jost", sans-serif;
    font-weight: 400;
    font-size: 23px;
    letter-spacing: 2px;
    color: var(--ink);
  }
  .person-title {
    position: absolute;
    left: 28px;
    top: 121px;
    font-family: "Jost", sans-serif;
    font-weight: 500;
    font-size: 12px;
    letter-spacing: 1.5px;
    color: var(--dark);
  }
  .address {
    position: absolute;
    left: 29px;
    top: 173px;
    font-family: "Open Sans", sans-serif;
    font-size: 14px;
    line-height: 17px;
    color: var(--grey-text);
  }
  .contact-list {
    position: absolute;
    left: 29px;
    top: 219px;
    margin: 0;
    padding: 0;
    list-style: none;
    font-family: "Open Sans", sans-serif;
    font-size: 14px;
    line-height: 17px;
    color: var(--grey-text);
  }
  .contact-list li {
    display: flex;
    align-items: center;
    gap: 3px;
  }
  .contact-icon {
    width: 11px;
    height: 11px;
    fill: var(--ink);
    flex: none;
  }
</style>
</head>
<body>
<main class="stage">
  <section class="card card-front">
    <div class="front-pattern" role="img" aria-label="Faint repeating brand mark pattern in lighter blue"></div>
    <div class="front-name">Belmont Ridge</div>
  </section>

  <section class="card card-back">
    <div class="back-logo">Belmont Ridge</div>
    <div class="person-name">DANIEL HARTLEY</div>
    <div class="person-title">PORTFOLIO MANAGER</div>
    <div class="address">Level 14 Harbour Tower, 52 Kent Street,<br>Sydney NSW 2000</div>
    <ul class="contact-list">
      <li>
        <svg class="contact-icon" viewBox="0 0 24 24" aria-hidden="true"><path d="M6.6 10.8a15 15 0 0 0 6.6 6.6l2.2-2.2c.3-.3.7-.4 1-.2 1.1.4 2.3.6 3.6.6.6 0 1 .4 1 1V20c0 .6-.4 1-1 1C10.6 21 3 13.4 3 4c0-.6.4-1 1-1h3.5c.6 0 1 .4 1 1 0 1.3.2 2.5.6 3.6.1.3 0 .7-.2 1z"/></svg>
        +02 9400 3175
      </li>
      <li>
        <svg class="contact-icon" viewBox="0 0 24 24" aria-hidden="true"><path d="M2 5h20v14H2z M3 6l9 7 9-7" stroke="#fff" stroke-width="1.5"/></svg>
        contact@belmont-ridge.com
      </li>
      <li>
        <svg class="contact-icon" viewBox="0 0 24 24" aria-hidden="true"><circle cx="12" cy="12" r="10"/><path d="M2 12h20M12 2c3 3 3 17 0 20M12 2c-3 3-3 17 0 20" stroke="#fff" stroke-width="1.4" fill="none"/></svg>
        www.belmont-ridge.com
      </li>
    </ul>
    <div class="back-band"></div>
  </section>
</main>
</body>
</html>
```